Payment company requires web design

We need a web design for a new company based in Singapore.

The company focuses on providing 2 key products: 1) an alternative payment option (i.e. like quib or trelloquin options) on the traditional checkout process 2) a replacement/outsource of a merchants payment page. Key in the UX flow is a end customer dashboard that manages all payments.

We look to provide a simple, fluid and easy to use payment process. The dashboard is minimalistic that allows easy navigation, review of transactions and all available options through gamification.

The final design should communicate ease of use, flexibility and transparency.

Target Market(s)

The value is for the merchant - retail/travel/insurance companies. However its the merchant's end customers that are the target and who the UX is built for.

Industry/Entity Type

It Company

Logo Text

zelnar

Number of Pages Required

5+ page

Colors
ec1f27

Requirements
Must have
• 7 pages mimicking UX flow
• payment page * 2 - 1) alternative payment type 2) outsource of merchants payment page to our business
• our landing page
• end customer verification page
• end customer registration
• customer dashboard
• UX flow in attached file
Nice to have
• open to ideas
• have asked for the logo to be added
• logo to have the colour red (chinese for prosperity)
• the company is all about flexibility, transparency in personal finance management with the option of instalment payments

```html
<!DOCTYPE html>
<html lang="en">
<head>
<meta charset="utf-8">
<title>Zelnar — Payment Processing</title>
<link rel="stylesheet" href="https://fonts.googleapis.com/css2?family=Montserrat:wght@300;400;500;600&display=swap">
<style>
  :root{
    --brand:#b3353a;
    --brand-dark:#a02d32;
    --ink:#555a60;
    --ink-soft:#8a8e93;
    --ink-faint:#c9cbcd;
    --rule:#eeeeee;
    --paper:#ffffff;
    --footer:#f7f7f7;
  }
  *{box-sizing:border-box;margin:0;padding:0}
  html,body{width:1200px;height:2190px;overflow:hidden;background:var(--paper)}
  body{position:relative;font-family:"Montserrat",sans-serif;color:var(--ink)}
  .abs{position:absolute}

  /* Hero */
  .hero{left:0;top:0;width:1200px;height:661px;
    background:
      radial-gradient(ellipse 420px 520px at 470px 300px, rgba(120,150,190,.55), transparent 70%),
      radial-gradient(ellipse 300px 200px at 1050px 180px, rgba(230,220,205,.5), transparent 70%),
      linear-gradient(100deg,#2b2624 0%,#4a3e37 25%,#6b5a4e 50%,#3d322d 75%,#2a2220 100%);}
  .hero-shade{left:0;top:0;width:1200px;height:661px;background:rgba(20,15,12,.25)}
  .logo{font-weight:500;letter-spacing:1px;text-transform:uppercase;font-size:27px;line-height:1}
  .hero .logo,.site-logo{color:#fff}
  .search{left:444px;top:44px;width:263px;height:33px;border:1.5px solid rgba(255,255,255,.85);border-radius:17px;
    color:#fff;font-size:9px;letter-spacing:.5px;padding:11px 0 0 15px}
  .search svg{position:absolute;right:12px;top:10px}
  .nav a{position:absolute;top:55px;color:#fff;font-size:10px;text-decoration:none;letter-spacing:.3px}
  .header-rule{left:190px;top:102px;width:818px;height:1px;background:rgba(255,255,255,.3)}
  .hero-title{left:0;width:1200px;top:346px;text-align:center;color:#fff;font-size:24px;font-weight:400;letter-spacing:.2px}
  .btn{display:flex;align-items:center;justify-content:center;border-radius:24px;font-size:12px;font-weight:500;letter-spacing:.3px;text-transform:uppercase}
  .btn-primary{background:var(--brand);color:#fff}
  .btn-light{background:#fff;color:var(--brand)}
  .slider-dots{left:567px;top:604px;display:flex;gap:10px}
  .slider-dots span{width:9px;height:9px;border-radius:50%;background:#fff}
  .slider-dots span.active{background:var(--brand)}

  /* About */
  .section-title{color:var(--brand);font-weight:400;font-size:25px;letter-spacing:.3px}
  .about-text{left:200px;top:800px;width:800px;text-align:center;font-size:12.5px;line-height:23px;color:var(--ink-soft)}
  .feature{width:240px;text-align:center;top:895px}
  .feature p{margin-top:22px;font-size:12px;color:var(--ink);letter-spacing:.3px;text-transform:uppercase}
  .rule{left:200px;width:797px;height:1px;background:var(--rule)}

  /* FAQ */
  .badge{width:40px;height:40px;border-radius:50%;background:var(--brand);color:#fff;display:flex;align-items:center;justify-content:center;font-size:22px;font-weight:300}
  .question{left:251px;top:1215px;width:470px;font-size:21px;font-weight:300;line-height:32px;color:var(--ink)}
  .answer{left:251px;top:1308px;width:460px;font-size:12px;line-height:22.5px;color:var(--ink-soft)}
  .terminal-art{left:759px;top:1234px;width:237px;height:204px;border-radius:18px;
    background:linear-gradient(150deg,#c44449 0%,#b3353a 55%,#9c2c31 100%)}

  /* Cards */
  .card{top:1587px;width:386px;height:270px;border-radius:28px;padding:44px 0 0 28px}
  .card-info{left:203px;background:var(--brand);color:#fff}
  .card-service{left:611px;border:1.5px solid #ececec;background:#fff}
  .card h3{display:flex;align-items:center;gap:16px;font-size:25px;font-weight:300;letter-spacing:.3px;text-transform:uppercase;margin-left:4px}
  .card-service h3{color:var(--ink-soft)}
  .card p{margin-top:26px;width:330px;font-size:16.5px;line-height:27px;font-weight:300}
  .card-service p{color:var(--ink-faint)}
  .card .btn{position:absolute;left:24px;top:204px;width:148px;height:43px}

  /* Footer */
  .footer{left:0;top:1946px;width:1200px;height:244px;background:var(--footer)}
  .footer .logo{color:var(--brand);font-size:27px}
  .footer-links{font-size:10px;line-height:22.5px;color:var(--ink);text-transform:uppercase;letter-spacing:.2px}
  .social{display:flex;gap:12px;font-size:10px;font-weight:600;color:var(--brand)}
  .social span:nth-child(n+2){color:#444}
  .footer-rule{left:0;top:2142px;width:1200px;height:1px;background:#e9e9e9}
  .copyright{left:0;width:1200px;top:2159px;text-align:center;font-size:9.5px;color:var(--ink);letter-spacing:.2px}
</style>
</head>
<body>

<!-- Hero -->
<section class="abs hero" role="img" aria-label="Photo of a woman in glasses tapping a card payment terminal at a cafe table"></section>
<div class="abs hero-shade"></div>
<div class="abs logo site-logo" style="left:190px;top:47px">Zelnar</div>
<div class="abs search">SEARCH
  <svg width="11" height="11" viewBox="0 0 12 12"><circle cx="5" cy="5" r="3.6" fill="none" stroke="#fff" stroke-width="1.8"/><line x1="7.6" y1="7.6" x2="11" y2="11" stroke="#fff" stroke-width="1.8"/></svg>
</div>
<nav class="nav">
  <a style="left:759px">ABOUT</a>
  <a style="left:832px">FAQ'S</a>
  <a style="left:899px">CONTACT US</a>
</nav>
<div class="abs header-rule"></div>
<h1 class="abs hero-title">WE ARE PAYMENT PROCESSING COMPANY FROM SINGAPORE</h1>
<a class="abs btn btn-primary" style="left:489px;top:404px;width:222px;height:44px">Get Started Now</a>
<div class="abs slider-dots"><span class="active"></span><span></span><span></span><span></span></div>

<!-- About -->
<h2 class="abs section-title" style="left:0;width:1200px;text-align:center;top:745px">ABOUT ZELNAR</h2>
<p class="abs about-text">Sed ut perspiciatis unde omnis iste natus error sit voluptatem accusantium doloremque laudantium, totam rem aperiam, eaque ipsa quae ab illo inventore veritatis et quasi architecto beatae vitae dicta sunt explicabo. Nemo enim ipsam voluptatem</p>

<div class="abs feature" style="left:206px">
  <svg width="38" height="32" viewBox="0 0 38 32"><g fill="none" stroke="var(--brand)" stroke-width="4.5" stroke-linecap="round"><path d="M3 8h7c8 0 10 16 18 16h4"/><path d="M3 24h7c3 0 5-2 6.5-5M21 12c1.5-2.5 3.5-4 7-4h4"/></g><path d="M31 2l6 6-6 6z M31 18l6 6-6 6z" fill="var(--brand)"/></svg>
  <p>Flexibility</p>
</div>
<div class="abs feature" style="left:479px">
  <svg width="38" height="34" viewBox="0 0 38 34"><path d="M37 1L1 15l10 4 2 13 6-8 9 7z" fill="var(--brand)"/><path d="M11 19L37 1 15 22" fill="#fff" opacity=".5"/></svg>
  <p>Transperency</p>
</div>
<div class="abs feature" style="left:752px">
  <svg width="38" height="32" viewBox="0 0 38 32"><rect x="1" y="7" width="36" height="24" rx="3" fill="var(--brand)"/><path d="M13 7V3h12v4" fill="none" stroke="var(--brand)" stroke-width="3"/><rect x="1" y="16" width="36" height="2" fill="#fff"/><rect x="16" y="14" width="6" height="6" fill="#fff"/></svg>
  <p>Instalment Payment</p>
</div>

<div class="abs rule" style="top:1070px"></div>

<!-- FAQ -->
<h2 class="abs section-title" style="left:206px;top:1146px">FAQ</h2>
<div class="abs badge" style="left:199px;top:1225px">Q</div>
<p class="abs question">Sed ut perspiciatis unde omnis iste natus error sit voluptatem accusantium doloremque&nbsp; ?</p>
<div class="abs badge" style="left:199px;top:1313px">A</div>
<p class="abs answer">&nbsp;ipsa quae ab illo inventore veritatis et quasi architecto beatae vitae dicta sunt explicabo. Nemo enim ipsam voluptatem quia voluptas sit aspernatur aut odit aut fugit, sed quia consequuntur magni dolores eos qui ratione</p>
<a class="abs btn btn-primary" style="left:200px;top:1423px;width:147px;height:44px">Read More</a>
<div class="abs terminal-art" role="img" aria-label="Illustration of a red card payment terminal"></div>

<div class="abs rule" style="top:1536px"></div>

<!-- Cards -->
<article class="abs card card-info">
  <h3><svg width="24" height="24" viewBox="0 0 24 24"><circle cx="12" cy="12" r="11" fill="#fff"/><rect x="10.3" y="10" width="3.4" height="9" fill="var(--brand)"/><circle cx="12" cy="6.5" r="2" fill="var(--brand)"/></svg>Information</h3>
  <p>Sed ut perspiciatis unde omnis iste natus error sit voluptatem accusantium doloremque.</p>
  <a class="btn btn-light">Read More</a>
</article>
<article class="abs card card-service">
  <h3><svg width="22" height="24" viewBox="0 0 22 24"><circle cx="11" cy="6.5" r="6" fill="var(--brand)"/><path d="M0 24c0-7 4-10.5 11-10.5S22 17 22 24z" fill="var(--brand)"/></svg>Customer Service</h3>
  <p>Sed ut perspiciatis unde omnis iste natus error sit voluptatem accusantium doloremque.</p>
  <a class="btn btn-primary">Read More</a>
</article>

<div class="abs rule" style="top:1915px"></div>

<!-- Footer -->
<footer class="abs footer"></footer>
<div class="abs footer logo" style="left:190px;top:2016px;width:auto;height:auto;background:none">Zelnar</div>
<ul class="abs footer-links" style="left:394px;top:2009px;list-style:none"><li>About</li><li>FAQ's</li><li>Contact Us</li></ul>
<ul class="abs footer-links" style="left:531px;top:2009px;list-style:none"><li>Leadership Team</li><li>Jobs</li></ul>
<ul class="abs footer-links" style="left:699px;top:2009px;list-style:none"><li>Terms of Use</li><li>Privacy Policy</li></ul>
<div class="abs social" style="left:874px;top:2019px"><span>Facely</span><span>Plusly</span><span>Chirpa</span><span>Vidoo</span></div>
<div class="abs footer-rule"></div>
<p class="abs copyright">© 2016 COMPANY NAME &nbsp;|&nbsp; ALL RIGHTS RESERVED</p>

</body>
</html>
```